Business Cards for a law firm

Business cards for our law firm. Use our silhoette logo and OAK PARTNERS - check our website (www.oakpartners.example)

Contact Information for Business Card

our silhouette logo, OAK PARTNERS, 800-555-0147, Dorian Pemberton, dorian@oakpartners.example

Requirements
Must have
• our silhouette logo, OAK PARTNERS, 800-555-0147, Dorian Pemberton, dorian@oakpartners.example

```html
<!DOCTYPE html>
<html lang="en">
<head>
<meta charset="utf-8">
<title>Oak Partners — Business Cards</title>
<link rel="stylesheet" href="https://fonts.googleapis.com/css2?family=Cinzel:wght@600&family=Roboto:wght@400&display=swap">
<style>
  :root {
    --backdrop: #16171b;
    --navy-deep: #0e1a4a;
    --navy: #132272;
    --royal: #1c2f8c;
    --pattern-dark: #0b1850;
    --pattern-light: #4c72c9;
    --rim: #3d5db4;
    --ink: #ffffff;
  }
  * { box-sizing: border-box; margin: 0; padding: 0; }
  html, body {
    width: 1200px; height: 840px; overflow: hidden;
    background: var(--backdrop);
  }
  .canvas { position: relative; width: 1200px; height: 840px; }

  .card {
    position: absolute;
    width: 640px; height: 366px;
    border-radius: 22px;
    overflow: hidden;
    border: 2px solid var(--rim);
    box-shadow: 0 18px 40px rgba(0,0,0,.55);
  }

  /* Front */
  .card--front { left: 150px; top: 30px; background: var(--navy-deep); }
  .card__pattern {
    position: absolute; inset: 0;
    background:
      radial-gradient(ellipse at 85% 70%, rgba(76,114,201,.85), rgba(76,114,201,0) 60%),
      linear-gradient(115deg, var(--pattern-dark) 0%, var(--navy) 45%, var(--royal) 70%, var(--pattern-light) 100%);
  }
  .brand {
    position: absolute; left: 0; right: 0; top: 50%;
    transform: translateY(-50%);
    display: flex; align-items: center; justify-content: center; gap: 16px;
  }
  .brand__mark {
    width: 26px; height: 26px; border-radius: 50%;
    background: var(--ink);
  }
  .brand__name {
    font-family: "Cinzel", serif;
    font-weight: 600;
    font-size: 46px;
    letter-spacing: 3px;
    color: var(--ink);
  }

  /* Back */
  .card--back {
    left: 410px; top: 444px;
    background: linear-gradient(100deg, var(--navy-deep) 0%, var(--navy) 38%, #15248a 58%, var(--navy-deep) 100%);
  }
  .holder {
    position: absolute; left: 40px; top: 198px;
    font-family: "Cinzel", serif; font-weight: 600;
    font-size: 24px; letter-spacing: 1.5px;
    white-space: nowrap;
    color: var(--ink);
  }
  .holder-mark {
    position: absolute; left: 340px; top: 150px;
    width: 22px; height: 22px; border-radius: 50%;
    background: var(--ink);
  }
  .contact {
    position: absolute; left: 378px; top: 136px;
    list-style: none;
    font-family: "Roboto", sans-serif;
    font-size: 15px; line-height: 24px;
    color: var(--ink);
  }
  .contact__item { display: flex; align-items: center; gap: 7px; white-space: nowrap; }
  .contact__icon { width: 14px; height: 14px; flex: none; }
</style>
</head>
<body>
<main class="canvas">
  <section class="card card--front" aria-label="Card front">
    <div class="card__pattern" role="img" aria-label="Repeating pattern of paired standing figures in shades of blue"></div>
    <div class="brand">
      <span class="brand__mark"></span>
      <span class="brand__name">OAK PARTNERS</span>
    </div>
  </section>

  <section class="card card--back" aria-label="Card back">
    <p class="holder">DORIAN PEMBERTON</p>
    <span class="holder-mark"></span>
    <ul class="contact">
      <li class="contact__item">
        <svg class="contact__icon" viewBox="0 0 16 16"><path fill="#fff" d="M3 1h3l1.5 3.5-2 1.3a9 9 0 0 0 4.7 4.7l1.3-2L15 10v3a2 2 0 0 1-2 2C6.4 15 1 9.6 1 3a2 2 0 0 1 2-2z"/></svg>
        800-555-0147
      </li>
      <li class="contact__item">
        <svg class="contact__icon" viewBox="0 0 16 16"><rect x="1" y="3" width="14" height="10" rx="1.5" fill="#fff"/><path d="M1.5 3.8 8 9l6.5-5.2" fill="none" stroke="#132272" stroke-width="1.4"/></svg>
        dorian@oakpartners.example
      </li>
      <li class="contact__item">
        <svg class="contact__icon" viewBox="0 0 16 16"><circle cx="8" cy="8" r="7" fill="#fff"/><path d="M1 8h14M8 1c-2.5 2-2.5 12 0 14M8 1c2.5 2 2.5 12 0 14" fill="none" stroke="#132272" stroke-width="1.1"/></svg>
        www.oakpartners.example
      </li>
    </ul>
  </section>
</main>
</body>
</html>
```